Business Card Design Project

Company Name - Solvane Care

Wellness consulting and training company. Run through a medical centre.

Main colour themes are orange and blue, as in the logo. Want to replicate same effect with business cards.

To give a sense of freedom and potential as per the company name.

Want the business card to be in line with stationary design, which I have launched as well.

Double sided with design and colour on one side and details on other side.

Reason: Need business card and stationary design to be teed up.

Target Market(s)

35 to 65 age group.
New age and trendy

Industry/Entity Type

Training

Requirements
Must have
• Colours orange and blue as per logo
Nice to have
• Design to be similar to stationary design, letterhead and envelopes

```html
<!DOCTYPE html>
<html lang="en">
<head>
<meta charset="utf-8">
<title>Solvane Care – Business Card</title>
<link rel="stylesheet" href="https://fonts.googleapis.com/css2?family=Lato:wght@400;700;900&display=swap">
<style>
  :root {
    --bg: #2c2c2e;
    --card: #ffffff;
    --card-shade: #eef0f3;
    --blue: #2f6db5;
    --blue-deep: #1f4f94;
    --blue-light: #5b93d3;
    --navy: #1e4f93;
    --orange: #e8620f;
    --tag-sub: #7a6a55;
    --white: #ffffff;
  }
  * { box-sizing: border-box; margin: 0; padding: 0; }
  html, body { width: 1200px; height: 997px; overflow: hidden; }
  body {
    background: var(--bg);
    font-family: "Lato", Arial, sans-serif;
    position: relative;
  }
  .card {
    position: absolute;
    left: 280px;
    width: 640px;
    height: 366px;
    background: linear-gradient(180deg, var(--card) 0%, var(--card-shade) 100%);
    overflow: hidden;
    box-shadow: 0 12px 30px rgba(0,0,0,.45);
  }
  .card--front { top: 90px; }
  .card--back { top: 511px; }

  /* bands with pinstripes */
  .band {
    position: absolute;
    left: 0; width: 100%;
    background: linear-gradient(180deg, var(--blue-light), var(--blue));
  }
  .band--top { top: 0; height: 22px; }
  .band--bottom { bottom: 0; height: 26px; background: linear-gradient(180deg, var(--blue), var(--blue-deep)); }
  .pinstripes {
    position: absolute; left: 0; width: 100%; height: 12px;
    background: repeating-linear-gradient(180deg, var(--blue-light) 0 1.5px, transparent 1.5px 4px);
  }
  .card--front .pinstripes--top { top: 25px; }
  .card--front .pinstripes--bottom { bottom: 29px; }

  /* wordmark */
  .wordmark {
    position: absolute;
    display: flex; align-items: center; gap: 12px;
    font-family: "Lato", Arial, sans-serif;
    font-weight: 400;
    color: var(--navy);
    white-space: nowrap;
  }
  .wordmark__dot {
    display: inline-block; border-radius: 50%;
    background: var(--orange);
  }
  .card--front .wordmark { left: 0; right: 0; top: 140px; justify-content: center; font-size: 62px; letter-spacing: -1px; }
  .card--front .wordmark__dot { width: 22px; height: 22px; }
  .card--back .wordmark { right: 42px; top: 60px; font-size: 46px; letter-spacing: -1px; }
  .card--back .wordmark__dot { width: 16px; height: 16px; }

  /* back side */
  .name-tag {
    position: absolute; left: 0; top: 100px;
    width: 208px; height: 30px;
    background: var(--orange);
    color: var(--white);
    font-weight: 900; font-size: 21px; letter-spacing: .5px;
    padding: 3px 0 0 40px;
  }
  .designation {
    position: absolute; left: 40px; top: 134px;
    font-size: 13px; font-weight: 700; color: var(--tag-sub);
  }
  .address {
    position: absolute; left: 0; right: 40px; top: 200px;
    text-align: right;
    font-size: 13.5px; font-weight: 900; letter-spacing: .3px;
    color: var(--orange); text-transform: uppercase;
  }
  .contact-panel {
    position: absolute; left: 0; bottom: 0; width: 100%; height: 140px;
    background: linear-gradient(180deg, rgba(47,109,181,0) 0%, rgba(47,109,181,.55) 35%, var(--blue-deep) 100%);
  }
  .contact-panel .pinstripes { top: 82px; background: repeating-linear-gradient(180deg, var(--white) 0 1.5px, transparent 1.5px 4px); opacity: .75; }
  .contact-list {
    position: absolute; list-style: none;
    color: var(--white); font-size: 17px; font-weight: 400;
  }
  .contact-list li { display: flex; align-items: center; gap: 12px; height: 28px; }
  .contact-list svg { width: 18px; height: 18px; fill: none; stroke: var(--white); stroke-width: 1.8; stroke-linecap: round; stroke-linejoin: round; opacity: .9; }
  .contact-list--phones { left: 70px; top: 236px; }
  .contact-list--web { left: 350px; top: 236px; font-size: 16px; }
</style>
</head>
<body>

  <section class="card card--front" aria-label="Business card front">
    <div class="band band--top"></div>
    <div class="pinstripes pinstripes--top"></div>
    <div class="wordmark"><span class="wordmark__dot"></span>Solvane Care</div>
    <div class="pinstripes pinstripes--bottom"></div>
    <div class="band band--bottom"></div>
  </section>

  <section class="card card--back" aria-label="Business card back">
    <div class="wordmark"><span class="wordmark__dot"></span>Solvane Care</div>
    <div class="name-tag">YOUR NAME</div>
    <div class="designation">Designation</div>
    <p class="address">Via dei Tigli, 14 60100 Ancona (AN), Italy</p>
    <div class="contact-panel"><div class="pinstripes"></div></div>

    <ul class="contact-list contact-list--phones">
      <li>
        <svg viewBox="0 0 24 24" aria-hidden="true"><path d="M3 9c0-3 4-4 9-4s9 1 9 4l-3 1-2-2H8L6 10z"/><rect x="6" y="12" width="12" height="8" rx="1"/></svg>
        +39 320 4418756
      </li>
      <li>
        <svg viewBox="0 0 24 24" aria-hidden="true"><path d="M5 3h4l2 5-3 2a12 12 0 0 0 6 6l2-3 5 2v4a2 2 0 0 1-2 2A17 17 0 0 1 3 5a2 2 0 0 1 2-2z"/></svg>
        (+321) 654 0987
      </li>
    </ul>

    <ul class="contact-list contact-list--web">
      <li>
        <svg viewBox="0 0 24 24" aria-hidden="true"><rect x="3" y="5" width="18" height="14" rx="1"/><path d="M3 6l9 7 9-7"/></svg>
        info@solvanecare.com
      </li>
      <li>
        <svg viewBox="0 0 24 24" aria-hidden="true"><path d="M10 14a4 4 0 0 0 6 0l3-3a4 4 0 0 0-6-6l-1 1"/><path d="M14 10a4 4 0 0 0-6 0l-3 3a4 4 0 0 0 6 6l1-1"/></svg>
        www.solvanecare.com
      </li>
    </ul>
  </section>

</body>
</html>
```